Company web site

Looking for a full responsive(mobile friendly) wordpress implementation

Some material is in the website -- brelvanto.wordpress.com

But looking for a template more consistent with the logo design, and more future looking.

Target Market(s)

Enterprise Clients

Industry/Entity Type

It Company

Font styles to use
Sans Serif

Colors
33a6d7
0255a3
0455a3
cfdeed
85abd2
3176b5

Requirements
Must have
• about, contact information, partner page, success stories, customer testimonials. links to social presence.
• pricing information

```html
<!DOCTYPE html>
<html lang="en">
<head>
<meta charset="utf-8">
<title>Brelvanto – Contact Us</title>
<link href="https://fonts.googleapis.com/css2?family=Exo+2:wght@400;500;600;700&family=Open+Sans:wght@400;600;700&display=swap" rel="stylesheet">
<style>
:root{
  --sky:#33a6d7;
  --navy:#0255a3;
  --ink:#3a3a3a;
  --muted:#666;
  --topbar:#5e5e5e;
  --line:#d6d6d6;
  --band:#f1f1f1;
  --footer:#16243a;
  --footer-text:#d4dce6;
  --white:#fff;
}
*{box-sizing:border-box;margin:0;padding:0}
html,body{width:786px;height:1200px;overflow:hidden;background:var(--white)}
body{position:relative;font-family:"Open Sans",sans-serif;color:var(--ink)}
h1,h2,h3,h4{font-weight:400}
.abs{position:absolute}

.topbar{left:0;top:0;width:786px;height:20px;background:var(--topbar);color:var(--white);font-size:8px;display:flex;align-items:center;padding-left:52px}
.topbar svg{margin-right:6px}
.topbar b{margin-left:3px}
.top-social{position:absolute;right:52px;top:0;display:flex;height:20px}
.top-social span{width:24px;height:20px;border-left:1px solid #777;display:flex;align-items:center;justify-content:center}
.top-social span:last-child{border-right:1px solid #777}
.top-social i{width:7px;height:7px;border-radius:50%;background:var(--white)}

.header{left:0;top:20px;width:786px;height:64px;background:var(--white)}
.brand{left:52px;top:40px;display:flex;align-items:center;gap:7px;font-family:"Exo 2",sans-serif;font-weight:700;font-size:18px;color:var(--sky)}
.brand i{width:26px;height:26px;border-radius:50%;background:var(--sky)}
.nav{left:367px;top:48px;display:flex;gap:25px;font-family:"Exo 2",sans-serif;font-size:11px;color:#555}
.nav-contact{left:668px;top:20px;width:65px;height:64px;background:var(--sky);color:var(--white);font-family:"Exo 2",sans-serif;font-weight:700;font-size:11px;display:flex;flex-direction:column;align-items:center;justify-content:center;gap:5px}

.hero{left:0;top:84px;width:786px;height:220px;background:linear-gradient(90deg,#040608 0%,#0b1622 45%,#1f4f78 72%,#2a6a9a 88%,#1a3550 100%)}
.hero-art{right:0;top:0;width:370px;height:220px;background:radial-gradient(ellipse at 55% 40%,#7bc4ef 0%,#3b82b8 30%,rgba(20,50,80,0) 70%)}
.hero-title{left:52px;top:92px;font-family:"Exo 2",sans-serif;font-weight:600;font-size:21px;line-height:27px;color:var(--white)}
.hero-title em{font-style:normal;color:var(--sky)}

.crumbs{left:0;top:304px;width:786px;height:26px;background:#e6e6e6;font-size:8.5px;font-weight:700;display:flex;align-items:center;padding-left:52px;gap:7px;color:#555}
.crumbs .current{color:var(--sky)}

.page-title{left:0;top:370px;width:786px;text-align:center;font-family:"Exo 2",sans-serif;font-size:24px;color:#444}
.page-title b{color:var(--navy);font-weight:700}
.title-rule{left:211px;top:408px;width:364px;height:12px}

.form-head{left:54px;top:436px;font-size:17px;color:#333}
.form-head-rule{left:52px;top:465px;width:60px;height:1px;background:#999}
.form-intro{left:52px;top:477px;width:360px;font-size:8px;line-height:17px;color:#555}
.label{font-size:9.5px;color:#333}
.label sup{color:#d23;font-size:9px;vertical-align:0;margin-left:2px}
.field{border:1px solid var(--line);background:var(--white)}
.submit{left:52px;top:753px;width:102px;height:27px;border:1px solid #777;border-radius:3px;font-family:"Exo 2",sans-serif;font-weight:600;font-size:10.5px;display:flex;align-items:center;justify-content:center;color:#444}
.map{left:492px;top:440px;width:294px;height:334px;background:linear-gradient(135deg,#eceae4 0%,#e3e1da 50%,#e9e6dd 100%)}

.info-band{left:0;top:827px;width:786px;height:146px;background:var(--band)}
.info{top:857px;width:232px;height:122px}
.info-icon{left:0;top:22px;width:40px;height:40px;border:1.5px solid var(--sky);border-radius:50%;background:var(--white);display:flex;align-items:center;justify-content:center}
.info-divider{left:48px;top:-5px;width:1px;height:98px;background:#d8d8d8}
.info-title{left:66px;top:4px;font-size:14.5px;color:#444}
.info-rule{left:66px;top:31px;width:150px;height:1px;background:#ddd}
.info-text{left:68px;top:44px;font-size:8.5px;line-height:17px;color:#555}

.footer{left:0;top:973px;width:786px;height:198px;background:var(--footer)}
.f-head{top:1006px;font-family:"Exo 2",sans-serif;font-weight:600;font-size:13px;color:var(--white)}
.f-head em{font-style:normal;color:var(--sky)}
.f-rule{top:1029px;height:1px;background:#3a4a60}
.links{left:53px;top:1042px;list-style:none;font-size:9.5px;line-height:18.6px;color:var(--footer-text)}
.links li::before{content:"•";color:var(--sky);margin-right:7px}
.links li.active{color:var(--sky);font-weight:600}
.f-contact{left:190px;top:1045px;font-size:9.5px;line-height:13px;width:180px;color:var(--footer-text)}
.f-contact strong{color:var(--white);font-size:10.5px}
.f-row{display:flex;align-items:center;gap:6px;margin-top:9px}
.f-map{left:384px;top:1048px;width:158px;height:100px;border:2px solid #cfd6de;background:linear-gradient(135deg,#dcdcd8,#c9c9c4)}
.f-brand{left:580px;top:1092px;width:154px;text-align:center;font-family:"Exo 2",sans-serif;font-weight:700;font-size:21px;color:var(--sky);display:flex;align-items:center;justify-content:center;gap:7px}
.f-brand i{width:22px;height:22px;border-radius:50%;background:var(--sky)}
.f-social{left:610px;top:1126px;display:flex;gap:17px}
.f-social i{width:8px;height:8px;border-radius:2px;background:#c9d3de}
.copyright{left:0;top:1171px;width:786px;height:29px;background:var(--sky);color:var(--white);font-size:9px;display:flex;align-items:center;justify-content:center}
.copyright b{margin:0 2px}
</style>
</head>
<body>

<div class="abs topbar">
  <svg width="9" height="9" viewBox="0 0 10 10"><path d="M2 1l2 2-1 1.2c.6 1.3 1.5 2.2 2.8 2.8L7 6l2 2-1.2 1.3C4.5 9 1 5.5.7 2.2z" fill="#fff"/></svg>
  Call Us : <b>+1 555 013 2468</b>
  <div class="top-social" aria-label="Social links"><span><i></i></span><span><i></i></span><span><i></i></span><span><i></i></span></div>
</div>

<div class="abs header"></div>
<div class="abs brand"><i></i>Brelvanto</div>
<nav class="abs nav"><span>Home</span><span>Platform</span><span>Partners</span><span>Blog</span><span>About</span></nav>
<div class="abs nav-contact">
  <svg width="16" height="14" viewBox="0 0 16 14"><path d="M2 5c0-2 3-3 6-3s6 1 6 3l-2 1-1-2H5L4 6z" fill="#fff"/><rect x="4" y="7" width="8" height="6" rx="2" fill="none" stroke="#fff" stroke-width="1.3"/><circle cx="8" cy="10" r="1.3" fill="#fff"/></svg>
  Contact
</div>

<section class="abs hero">
  <div class="abs hero-art" role="img" aria-label="Hand holding a tablet projecting a glowing globe and floating network icons"></div>
  <h1 class="abs hero-title">Bridging <em>Connected Devices</em><br>With <em>Enterprise Solutions</em></h1>
</section>

<div class="abs crumbs"><span>HOME</span><span style="color:var(--sky)">»</span><span class="current">CONTACT US</span></div>

<h2 class="abs page-title">CONTACT <b>US</b></h2>
<svg class="abs title-rule" viewBox="0 0 364 12"><line x1="0" y1="6" x2="166" y2="6" stroke="#ccc"/><line x1="198" y1="6" x2="364" y2="6" stroke="#ccc"/><circle cx="182" cy="6" r="5" fill="none" stroke="#bbb" stroke-width="1.5"/></svg>

<h3 class="abs form-head">Sent Us A Message</h3>
<div class="abs form-head-rule"></div>
<p class="abs form-intro">Feel free to contact us via our contact form below. One of our staff will respond to your enquiry within 2 business days.</p>

<label class="abs label" style="left:52px;top:514px">Name<sup>*</sup></label>
<div class="abs field" style="left:52px;top:529px;width:200px;height:27px"></div>
<label class="abs label" style="left:270px;top:514px">Email<sup>*</sup></label>
<div class="abs field" style="left:270px;top:529px;width:200px;height:27px"></div>
<label class="abs label" style="left:52px;top:567px">Phone</label>
<div class="abs field" style="left:52px;top:582px;width:200px;height:27px"></div>
<label class="abs label" style="left:270px;top:567px">Subject<sup>*</sup></label>
<div class="abs field" style="left:270px;top:582px;width:200px;height:27px"></div>
<label class="abs label" style="left:52px;top:619px">Message<sup>*</sup></label>
<div class="abs field" style="left:52px;top:634px;width:418px;height:103px"></div>
<div class="abs submit">Submit</div>

<div class="abs map" role="img" aria-label="Street map of the office area"></div>

<div class="abs info-band"></div>

<div class="abs info" style="left:52px">
  <div class="abs info-icon"><svg width="16" height="18" viewBox="0 0 16 18"><path d="M8 1a6 6 0 0 1 6 6c0 4-6 10-6 10S2 11 2 7a6 6 0 0 1 6-6z" fill="var(--sky)"/><circle cx="8" cy="7" r="2.3" fill="#fff"/></svg></div>
  <div class="abs info-divider"></div>
  <div class="abs info-title">Address</div>
  <div class="abs info-rule"></div>
  <div class="abs info-text">418 Harlow Ave<br>Larkspur Bay, CA 90210</div>
</div>
<div class="abs info" style="left:285px">
  <div class="abs info-icon"><svg width="20" height="16" viewBox="0 0 20 16"><rect x="1" y="1" width="18" height="14" rx="1" fill="var(--sky)"/><path d="M1 1l9 8 9-8" fill="none" stroke="#fff" stroke-width="1.4"/></svg></div>
  <div class="abs info-divider"></div>
  <div class="abs info-title">Email Address</div>
  <div class="abs info-rule"></div>
  <div class="abs info-text">info@brelvanto.com<br>demo@brelvanto.com</div>
</div>
<div class="abs info" style="left:518px">
  <div class="abs info-icon"><svg width="20" height="18" viewBox="0 0 20 18"><path d="M1 7c0-3 4-5 9-5s9 2 9 5l-3 1.5-1.5-3h-9L4 8.5z" fill="var(--sky)"/><rect x="5" y="9" width="10" height="8" rx="2.5" fill="var(--sky)"/><circle cx="10" cy="13" r="1.8" fill="#fff"/></svg></div>
  <div class="abs info-divider"></div>
  <div class="abs info-title">Contact No</div>
  <div class="abs info-rule"></div>
  <div class="abs info-text">+1-(888) 555-0142<br>555-013-2469</div>
</div>

<footer class="abs footer"></footer>
<h4 class="abs f-head" style="left:53px">Quick <em>Links</em></h4>
<div class="abs f-rule" style="left:53px;width:86px"></div>
<ul class="abs links">
  <li class="active">Home</li><li>Platform</li><li>Partners</li><li>Blog</li><li>About</li><li>Contact</li>
</ul>

<h4 class="abs f-head" style="left:190px">Contact <em>Details</em></h4>
<div class="abs f-rule" style="left:190px;width:110px"></div>
<div class="abs f-contact">
  <strong>Brelvanto</strong><br>123, Lorem ipsum dolor sit amet,<br>euismod - 123 456
  <div class="f-row"><svg width="9" height="9" viewBox="0 0 10 10"><path d="M2 1l2 2-1 1.2c.6 1.3 1.5 2.2 2.8 2.8L7 6l2 2-1.2 1.3C4.5 9 1 5.5.7 2.2z" fill="var(--sky)"/></svg>555 013 2468</div>
  <div class="f-row"><svg width="9" height="9" viewBox="0 0 10 10"><rect x="2" y="0.5" width="6" height="3" fill="var(--sky)"/><rect x="0.5" y="3.5" width="9" height="4" fill="var(--sky)"/><rect x="2" y="6.5" width="6" height="3" fill="none" stroke="var(--sky)"/></svg>555 013 2468</div>
  <div class="f-row"><svg width="9" height="7" viewBox="0 0 10 8"><rect x="0.5" y="0.5" width="9" height="7" fill="var(--sky)"/><path d="M.5.5l4.5 4 4.5-4" fill="none" stroke="var(--footer)"/></svg>info@brelvanto.com</div>
</div>

<h4 class="abs f-head" style="left:384px">Location <em>Map</em></h4>
<div class="abs f-rule" style="left:384px;width:100px"></div>
<div class="abs f-map" role="img" aria-label="Small street map marking 418 Harlow Avenue"></div>

<div class="abs f-brand"><i></i>Brelvanto</div>
<div class="abs f-social" aria-label="Social links"><i></i><i></i><i></i><i></i></div>

<div class="abs copyright">Copyright © 2017 <b>Brelvanto</b>. All Right Reserved.</div>

</body>
</html>
```